New Business Card Design Project

Use the flyer uploaded and website www.brightoakbuilders.com for inspiration.
List Our Services on Backside of business cards
Marcus Delling
Harborline Builders Inc.
Licensed General Contractors
858-471-6093

Contact Information for Business Card

Use the flyer uploaded and website www.brightoakbuilders.com for inspiration. List Our Services on Backside of business cards Marcus Delling Harborline Builders Inc. Licensed General Contractors 858-471-6093

```html
<!DOCTYPE html>
<html lang="en">
<head>
<meta charset="utf-8">
<title>Harborline Builders – Business Card</title>
<link href="https://fonts.googleapis.com/css2?family=Roboto:wght@400;500;700;900&display=swap" rel="stylesheet">
<style>
  :root{
    --stage:#232323;
    --card-dark:#1f1f20;
    --card-light:#ffffff;
    --red:#e21b23;
    --blue:#4f73c4;
    --ink:#1a1a1a;
    --paper-text:#f2f2f2;
  }
  *{box-sizing:border-box;margin:0;padding:0}
  html,body{width:1200px;height:780px;overflow:hidden}
  body{background:var(--stage);font-family:"Roboto",Arial,sans-serif;position:relative}
  .card{
    position:absolute;top:230px;width:560px;height:320px;border-radius:22px;
    border-bottom:4px solid var(--red);border-left:2px solid var(--red);
    box-shadow:0 14px 30px rgba(0,0,0,.55);overflow:hidden;
  }
  .card--back{left:30px;background:var(--card-dark);color:var(--paper-text)}
  .card--front{left:610px;background:var(--card-light);color:var(--ink)}

  .brand{display:flex;align-items:center;gap:10px;font-weight:400;letter-spacing:3px;text-transform:uppercase}
  .brand__dot{width:14px;height:14px;border-radius:50%;background:currentColor}

  /* back */
  .card--back .brand{position:absolute;top:70px;left:0;right:0;justify-content:center;font-size:30px}
  .guarantee{position:absolute;top:150px;left:0;right:0;text-align:center;font-weight:900;color:var(--red);font-size:15px;letter-spacing:.3px}
  .specialty{position:absolute;top:172px;left:0;right:0;text-align:center;font-weight:900;color:var(--blue);font-size:14px}
  .services{position:absolute;top:202px;left:20px;right:20px;list-style:none;display:flex;flex-wrap:wrap;justify-content:center;row-gap:6px;column-gap:10px;font-size:11.5px;font-weight:500}
  .services li{display:flex;align-items:center;gap:4px;white-space:nowrap}
  .tick{width:11px;height:11px;flex:none}

  /* front */
  .card--front .brand{position:absolute;top:92px;left:34px;font-size:26px}
  .holder{position:absolute;top:40px;right:0;text-align:right}
  .holder__name{display:inline-block;color:var(--red);font-weight:900;font-size:30px;letter-spacing:.5px;padding-right:14px;border-right:12px solid var(--red);line-height:1}
  .holder__title{font-size:13px;font-weight:500;padding-right:26px;margin-top:6px}
  .contact{position:absolute;left:34px;bottom:30px;list-style:none;font-size:14px;font-weight:500}
  .contact__company{margin-bottom:14px;font-size:14px}
  .contact li{display:flex;align-items:center;gap:10px;margin-top:6px}
  .icon{width:16px;height:16px;flex:none;fill:var(--red)}
</style>
</head>
<body>

<section class="card card--back" aria-label="Card back – services">
  <div class="brand"><span class="brand__dot"></span>Harborline Builders</div>
  <p class="guarantee">OUR SERVICES ARE 100% GUARANTEED</p>
  <p class="specialty">SPECIALIZING IN:</p>
  <ul class="services">
    <li><svg class="tick" viewBox="0 0 12 12"><circle cx="6" cy="6" r="5" fill="none" stroke="#e21b23" stroke-width="1.2"/><path d="M3.5 6.2l1.8 1.8 3.3-3.6" fill="none" stroke="#e21b23" stroke-width="1.4"/></svg>Remodel: Kitchen &amp; Bath</li>
    <li><svg class="tick" viewBox="0 0 12 12"><circle cx="6" cy="6" r="5" fill="none" stroke="#e21b23" stroke-width="1.2"/><path d="M3.5 6.2l1.8 1.8 3.3-3.6" fill="none" stroke="#e21b23" stroke-width="1.4"/></svg>Painting: Interior &amp; Exterior</li>
    <li><svg class="tick" viewBox="0 0 12 12"><circle cx="6" cy="6" r="5" fill="none" stroke="#e21b23" stroke-width="1.2"/><path d="M3.5 6.2l1.8 1.8 3.3-3.6" fill="none" stroke="#e21b23" stroke-width="1.4"/></svg>Flooring: Carpet, Vinyl, Wood</li>
    <li><svg class="tick" viewBox="0 0 12 12"><circle cx="6" cy="6" r="5" fill="none" stroke="#e21b23" stroke-width="1.2"/><path d="M3.5 6.2l1.8 1.8 3.3-3.6" fill="none" stroke="#e21b23" stroke-width="1.4"/></svg>Window &amp; Door Replacement</li>
    <li><svg class="tick" viewBox="0 0 12 12"><circle cx="6" cy="6" r="5" fill="none" stroke="#e21b23" stroke-width="1.2"/><path d="M3.5 6.2l1.8 1.8 3.3-3.6" fill="none" stroke="#e21b23" stroke-width="1.4"/></svg>Plumbing: Repairs &amp; Upgrades</li>
    <li><svg class="tick" viewBox="0 0 12 12"><circle cx="6" cy="6" r="5" fill="none" stroke="#e21b23" stroke-width="1.2"/><path d="M3.5 6.2l1.8 1.8 3.3-3.6" fill="none" stroke="#e21b23" stroke-width="1.4"/></svg>Energy-Efficient Upgrades</li>
    <li><svg class="tick" viewBox="0 0 12 12"><circle cx="6" cy="6" r="5" fill="none" stroke="#e21b23" stroke-width="1.2"/><path d="M3.5 6.2l1.8 1.8 3.3-3.6" fill="none" stroke="#e21b23" stroke-width="1.4"/></svg>Deck &amp; Patio Construction</li>
    <li><svg class="tick" viewBox="0 0 12 12"><circle cx="6" cy="6" r="5" fill="none" stroke="#e21b23" stroke-width="1.2"/><path d="M3.5 6.2l1.8 1.8 3.3-3.6" fill="none" stroke="#e21b23" stroke-width="1.4"/></svg>Water &amp; Mold Damage</li>
    <li><svg class="tick" viewBox="0 0 12 12"><circle cx="6" cy="6" r="5" fill="none" stroke="#e21b23" stroke-width="1.2"/><path d="M3.5 6.2l1.8 1.8 3.3-3.6" fill="none" stroke="#e21b23" stroke-width="1.4"/></svg>Garage Renovation</li>
  </ul>
</section>

<section class="card card--front" aria-label="Card front – contact">
  <div class="brand"><span class="brand__dot"></span>Harborline Builders</div>
  <div class="holder">
    <p class="holder__name">MARCUS DELLING</p>
    <p class="holder__title">Licensed General Contractors</p>
  </div>
  <ul class="contact">
    <li class="contact__company">Harborline Builders Inc.</li>
    <li><svg class="icon" viewBox="0 0 24 24"><path d="M6.6 10.8a15 15 0 0 0 6.6 6.6l2.2-2.2a1 1 0 0 1 1-.25 11.4 11.4 0 0 0 3.6.57 1 1 0 0 1 1 1V20a1 1 0 0 1-1 1A17 17 0 0 1 3 4a1 1 0 0 1 1-1h3.5a1 1 0 0 1 1 1c0 1.25.2 2.45.57 3.57a1 1 0 0 1-.25 1z"/></svg>858-471-6093</li>
    <li><svg class="icon" viewBox="0 0 24 24"><path d="M3 5h18a1 1 0 0 1 1 1v12a1 1 0 0 1-1 1H3a1 1 0 0 1-1-1V6a1 1 0 0 1 1-1zm1 2.2V17h16V7.2l-8 5.3z M4.5 7l7.5 5 7.5-5z"/></svg>info@brightoakbuilders.com</li>
    <li><svg class="icon" viewBox="0 0 24 24"><path d="M12 2a10 10 0 1 0 0 20 10 10 0 0 0 0-20zm6.9 6h-3a15.7 15.7 0 0 0-1.3-3.9A8 8 0 0 1 18.9 8zM12 4c.8 1.2 1.5 2.5 1.9 4h-3.8c.4-1.5 1.1-2.8 1.9-4zM4.3 14a8 8 0 0 1 0-4h3.4a16 16 0 0 0 0 4zm.8 2h3a15.7 15.7 0 0 0 1.3 3.9A8 8 0 0 1 5.1 16zm3-8h-3a8 8 0 0 1 4.3-3.9A15.7 15.7 0 0 0 8.1 8zM12 20c-.8-1.2-1.5-2.5-1.9-4h3.8c-.4 1.5-1.1 2.8-1.9 4zm2.3-6H9.7a14 14 0 0 1 0-4h4.6a14 14 0 0 1 0 4zm.3 5.9a15.7 15.7 0 0 0 1.3-3.9h3a8 8 0 0 1-4.3 3.9zm1.7-5.9a16 16 0 0 0 0-4h3.4a8 8 0 0 1 0 4z"/></svg>www.brightoakbuilders.com</li>
  </ul>
</section>

</body>
</html>
```